Business Card Design

Hi I need a business card designed, we already have the business name logo artwork and would like some concept ideas for the Bus Card layout.
On the back of the card i want to include the products and services that we offer.
We are a Plastics Sheeting manufacture based in Perth Australia.

                                       

We need a BC design for a company called Tarvo Plastics based in Perth Australia.

We supply from DIY to Trade & Industrial  Engineering Markets.

We specialise in:

·         Cut to size panels  (all shapes and sizes)

·         Plastics fabrication & Welding

·         Custom Designs

·         Plastic Repairs

·         PVC Pipe Slotting & PVC Pipe Threading

·         Supplier of all types of engineering plastics and profiles.

Including:           Acrylic / Clarvene

                               Polycarbonate / Dorvil

                               Prismatic Light Diffuser

                               Vantrib

                               HDPE / UHMWPE

                               PVC / PVC Foam

                               Nylon

                               HIPS

```html
<!DOCTYPE html>
<html lang="en">
<head>
<meta charset="utf-8">
<title>Tarvo Plastics — Business Card</title>
<link href="https://fonts.googleapis.com/css2?family=Source+Sans+3:ital,wght@0,400;0,600;0,700;1,700&display=swap" rel="stylesheet">
<style>
  :root {
    --navy: #1d2a5e;
    --orange: #e2792a;
    --bullet: #2b8fd4;
    --ink: #4d4f55;
    --paper: #ffffff;
    --backdrop: #e6e7ec;
    --rule: #c9cad0;
  }
  * { box-sizing: border-box; margin: 0; padding: 0; }
  html, body { width: 1200px; height: 987px; overflow: hidden; }
  body {
    background: var(--backdrop);
    font-family: "Source Sans 3", "Myriad Pro", Arial, sans-serif;
    color: var(--ink);
    position: relative;
  }
  .card {
    position: absolute;
    left: 240px;
    width: 720px;
    height: 440px;
    background: var(--paper);
    border-radius: 26px;
    overflow: hidden;
    box-shadow: 0 6px 18px rgba(30, 35, 60, .18);
  }
  .card--front { top: 36px; }
  .card--back { top: 511px; }

  /* Front */
  .brand {
    position: absolute;
    top: 56px; left: 0; width: 100%;
    display: flex; align-items: center; justify-content: center; gap: 18px;
  }
  .brand__mark { width: 34px; height: 34px; background: var(--orange); }
  .brand__name {
    font-size: 68px; font-weight: 700; color: var(--navy);
    letter-spacing: -0.5px; line-height: 1;
  }
  .person {
    position: absolute; top: 160px; left: 70px; width: 240px; text-align: right;
  }
  .person__name { font-size: 26px; font-weight: 700; color: var(--navy); line-height: 1.1; }
  .person__title { font-size: 18px; color: var(--orange); margin-bottom: 8px; }
  .person__address { font-size: 17px; line-height: 1.28; font-style: normal; }
  .divider {
    position: absolute; top: 168px; left: 336px; width: 1px; height: 136px;
    background: var(--rule);
  }
  .contacts {
    position: absolute; top: 170px; left: 360px; list-style: none;
    font-size: 19px; line-height: 1;
  }
  .contacts li { display: flex; align-items: center; gap: 12px; height: 34px; }
  .contacts svg { width: 18px; height: 18px; flex: none; }
  .band { position: absolute; left: 0; top: 0; width: 720px; height: 440px; }
  .legal {
    position: absolute; left: 40px; bottom: 16px;
    font-size: 16px; color: var(--paper); letter-spacing: .2px;
  }

  /* Back */
  .offer {
    position: absolute; inset: 34px 40px; text-align: center; color: var(--ink);
  }
  .offer__lead {
    font-size: 20px; font-weight: 700; font-style: italic; color: var(--navy);
    line-height: 1.2; margin-bottom: 16px;
  }
  .offer__heading {
    font-size: 24px; font-weight: 700; color: var(--navy); margin-bottom: 6px;
  }
  .offer__list {
    list-style: none; display: flex; flex-wrap: wrap; justify-content: center;
    column-gap: 20px; row-gap: 2px; font-size: 18px; line-height: 1.3;
    margin: 0 auto 14px;
  }
  .offer__list li::before {
    content: "•"; color: var(--bullet); margin-right: 5px;
  }
  .offer__list--services { max-width: 600px; }
  .offer__list--materials { max-width: 560px; }
</style>
</head>
<body>

<section class="card card--front" aria-label="Business card front">
  <svg class="band" viewBox="0 0 720 440" aria-hidden="true">
    <path d="M0,326 C200,332 420,400 720,424 L720,432 C420,410 200,346 0,344 Z" fill="var(--orange)"/>
    <path d="M0,356 C200,360 420,414 720,434 L720,440 L0,440 Z" fill="var(--navy)"/>
  </svg>

  <div class="brand">
    <span class="brand__mark"></span>
    <span class="brand__name">Tarvo Plastics</span>
  </div>

  <div class="person">
    <p class="person__name">Your Name</p>
    <p class="person__title">Title</p>
    <address class="person__address">
      Unit 4/18 Marlow Crescent<br>
      Brenton Park WA 6158<br>
      PO Box 2284<br>
      Brenton Park DC WA 6972
    </address>
  </div>

  <div class="divider"></div>

  <ul class="contacts">
    <li>
      <svg viewBox="0 0 20 20" aria-label="Phone"><circle cx="10" cy="10" r="9" fill="none" stroke="var(--orange)" stroke-width="2"/><path d="M7,5 L9,5 L9.5,8 L8.3,9 C9,10.5 10,11.5 11,12 L12,10.6 L15,11.2 L15,13 C11,14 6,9 7,5 Z" fill="var(--orange)"/></svg>
      08 9431 7750
    </li>
    <li>
      <svg viewBox="0 0 20 20" aria-label="Mobile"><rect x="5" y="1" width="10" height="18" rx="2" fill="var(--orange)"/><rect x="7" y="4" width="6" height="8" fill="#fff"/></svg>
      0400 555 218
    </li>
    <li>
      <svg viewBox="0 0 20 20" aria-label="Fax"><rect x="5" y="2" width="10" height="6" fill="var(--orange)"/><rect x="1" y="8" width="18" height="9" rx="2" fill="var(--orange)"/><rect x="6" y="12" width="8" height="2" fill="#fff"/></svg>
      08 9431 7751
    </li>
    <li>
      <svg viewBox="0 0 20 20" aria-label="Email"><rect x="1" y="4" width="18" height="12" rx="1.5" fill="var(--orange)"/><path d="M2,5 L10,11 L18,5" fill="none" stroke="#fff" stroke-width="1.6"/></svg>
      sales@tarvoplastics.com.au
    </li>
  </ul>

  <p class="legal">Tarvo Holdings Pty Ltd T/A Tarvo Plastics ABN: TBA</p>
</section>

<section class="card card--back" aria-label="Business card back">
  <div class="offer">
    <p class="offer__lead">The Products And Services That We Offer<br>Are Supplied From DIY To Trade &amp; Industrial Engineering Markets</p>

    <h2 class="offer__heading">We specialise in:</h2>
    <ul class="offer__list offer__list--services">
      <li>Cut to size panels (all shapes and sizes)</li>
      <li>Plastics fabrication &amp; Welding</li>
      <li>Custom Designs</li>
      <li>Plastic Repairs</li>
      <li>PVC Pipe Slotting &amp; PVC Pipe Threading</li>
      <li>Supplier of all types of engineering plastics and profiles</li>
    </ul>

    <h2 class="offer__heading">Including:</h2>
    <ul class="offer__list offer__list--materials">
      <li>Acrylic / Clarvene</li>
      <li>Polycarbonate / Dorvil</li>
      <li>Prismatic Light Diffuser</li>
      <li>Vantrib</li>
      <li>HDPE / UHMWPE</li>
      <li>PVC / PVC Foam</li>
      <li>Nylon</li>
      <li>HIPS</li>
    </ul>
  </div>
</section>

</body>
</html>
```